Business Card for Professional Photographer

I'm looking for an eye catching modern clean design that compliments my logo/ website fonts & colours.
I specialise in architecture, corporate & commercial photography so I'm marketing to professional clients rather than portrait / wedding clients.

I would prefer to not have a solid black design.

My logo brand guide is as follows :

Main front font. : Reislust
Main font colour : #fff
Slogan front font : Ubuntu Bold
Monogram front font : Venti Medium
Container colour : #fff

I need print ready files in pdf .png & .eps formats.

Included in the files below are some screen grabs as reference to font & colours etc.

```html
<!DOCTYPE html>
<html lang="en">
<head>
<meta charset="utf-8">
<title>Northlight Studio – Business Card</title>
<link rel="stylesheet" href="https://fonts.googleapis.com/css2?family=Ubuntu:wght@400;500;700&family=Roboto:wght@400&family=Saira+Semi+Condensed:wght@700&display=swap">
<style>
  :root {
    --stage: #3a3a3c;
    --card-black: #141416;
    --tile-navy: #2a3244;
    --tile-slate: #3a4150;
    --tile-sand: #5a4a36;
    --tile-umber: #3f3326;
    --tile-sky: #4b5a6e;
    --tile-stone: #6a6458;
    --tile-ink: #1e2430;
    --veil: rgba(12, 12, 14, 0.55);
    --gold: #d9ab3c;
    --gold-light: #f1d27a;
    --white: #ffffff;
  }
  * { box-sizing: border-box; margin: 0; padding: 0; }
  html, body { width: 799px; height: 1200px; overflow: hidden; }
  body { background: var(--stage); font-family: "Ubuntu", sans-serif; }

  .canvas {
    width: 799px;
    height: 1200px;
    display: flex;
    flex-direction: column;
    align-items: center;
    justify-content: space-around;
    padding: 60px 0;
  }

  .card {
    position: relative;
    width: 680px;
    height: 390px;
    border-radius: 4px;
    overflow: hidden;
    box-shadow: 0 18px 36px rgba(0,0,0,0.45);
  }

  /* Front */
  .card--front { background: var(--card-black); }
  .photo-grid {
    position: absolute;
    inset: 0;
    display: grid;
    grid-template-columns: 30% 22% 48%;
    grid-template-rows: 34% 33% 33%;
    gap: 2px;
    background: #0c0c0e;
  }
  .photo-tile { display: block; }
  .photo-tile--a { background: linear-gradient(160deg, var(--tile-umber), var(--tile-navy)); }
  .photo-tile--b { background: linear-gradient(180deg, var(--tile-stone), var(--tile-umber)); grid-row: span 2; }
  .photo-tile--c { background: linear-gradient(140deg, var(--tile-sky), var(--tile-slate)); grid-row: span 2; }
  .photo-tile--d { background: linear-gradient(200deg, var(--tile-navy), var(--tile-sky)); grid-row: span 2; }
  .photo-tile--e { background: linear-gradient(150deg, var(--tile-slate), var(--tile-ink)); }
  .photo-tile--f { background: linear-gradient(170deg, var(--tile-sand), var(--tile-umber)); }
  .front__veil { position: absolute; inset: 0; background: var(--veil); }

  .front__brand {
    position: absolute;
    left: 56px;
    top: 96px;
    display: flex;
    align-items: center;
    gap: 24px;
  }
  .brand-mark {
    width: 92px;
    height: 92px;
    border-radius: 50%;
    border: 6px solid var(--gold);
    flex-shrink: 0;
  }
  .brand-name {
    font-family: "Ubuntu", sans-serif;
    font-weight: 400;
    color: var(--gold);
    letter-spacing: 0.14em;
    text-transform: uppercase;
    line-height: 1;
    white-space: nowrap;
  }
  .brand-tagline {
    font-family: "Ubuntu", sans-serif;
    font-weight: 700;
    color: var(--gold);
    letter-spacing: 0.1em;
    line-height: 1;
    white-space: nowrap;
  }
  .front__brand .brand-name { font-size: 32px; margin-top: 58px; }
  .front__brand .brand-tagline { font-size: 12px; margin-top: 8px; }
  .front__url {
    position: absolute;
    left: 64px;
    bottom: 92px;
    font-size: 19px;
    letter-spacing: 0.14em;
    color: var(--gold-light);
  }

  /* Back */
  .card--back { background: var(--card-black); }
  .back__mark {
    position: absolute;
    left: 34px;
    top: 92px;
    width: 230px;
    height: 230px;
    border-radius: 50%;
    border: 18px solid var(--gold);
  }
  .back__brand {
    position: absolute;
    right: 40px;
    top: 64px;
    text-align: right;
  }
  .back__brand .brand-name { font-size: 28px; }
  .back__brand .brand-tagline { font-size: 11px; margin-top: 7px; }

  .back__person {
    position: absolute;
    right: 40px;
    top: 172px;
    text-align: right;
  }
  .person-name {
    font-family: "Saira Semi Condensed", sans-serif;
    font-weight: 700;
    font-size: 25px;
    color: var(--gold);
    line-height: 1.1;
  }
  .person-role {
    font-family: "Roboto", sans-serif;
    font-size: 17px;
    color: var(--white);
  }
  .contact-list {
    list-style: none;
    margin-top: 14px;
    font-family: "Roboto", sans-serif;
    font-size: 17px;
    color: var(--white);
    line-height: 1.38;
  }
  .contact-list li {
    display: flex;
    justify-content: flex-end;
    align-items: center;
    gap: 10px;
    white-space: nowrap;
  }
  .contact-icon { width: 15px; height: 15px; flex-shrink: 0; }
  .contact-icon--blank { width: 15px; flex-shrink: 0; }
</style>
</head>
<body>
<main class="canvas">

  <section class="card card--front" aria-label="Card front">
    <div class="photo-grid">
      <span class="photo-tile photo-tile--a" role="img" aria-label="Darkened commercial interior photograph"></span>
      <span class="photo-tile photo-tile--b" role="img" aria-label="Darkened corporate detail photograph"></span>
      <span class="photo-tile photo-tile--c" role="img" aria-label="Darkened modern building facade photograph"></span>
      <span class="photo-tile photo-tile--d" role="img" aria-label="Darkened waterfront architecture photograph"></span>
      <span class="photo-tile photo-tile--e" role="img" aria-label="Darkened product photograph"></span>
      <span class="photo-tile photo-tile--f" role="img" aria-label="Darkened interior design photograph"></span>
    </div>
    <div class="front__veil"></div>
    <div class="front__brand">
      <span class="brand-mark" aria-hidden="true"></span>
      <div>
        <p class="brand-name">Northlight Studio</p>
        <p class="brand-tagline">Architecture Corporate Commercial</p>
      </div>
    </div>
    <p class="front__url">www.northlightstudio.com.au</p>
  </section>

  <section class="card card--back" aria-label="Card back">
    <span class="back__mark" aria-hidden="true"></span>
    <div class="back__brand">
      <p class="brand-name">Northlight Studio</p>
      <p class="brand-tagline">Architecture Corporate commercial</p>
    </div>
    <div class="back__person">
      <p class="person-name">Mara Ellison</p>
      <p class="person-role">Photographer</p>
      <ul class="contact-list">
        <li>0400 218 576
          <svg class="contact-icon" viewBox="0 0 16 16" aria-hidden="true"><path fill="#d9ab3c" d="M4 1.5 6.3 4 5 5.6c.9 2 2.4 3.5 4.4 4.4L11 8.7l2.5 2.3-1.6 2.6C6.4 13.3 2.7 9.6 1.4 4.1z"/></svg>
        </li>
        <li>info@northlightstudio.com.au
          <svg class="contact-icon" viewBox="0 0 16 16" aria-hidden="true"><rect x="1" y="3.5" width="14" height="9" fill="#d9ab3c"/><path d="M1 3.5 8 9l7-5.5" fill="none" stroke="#141416" stroke-width="1.2"/></svg>
        </li>
        <li>www.northlightstudio.com.au
          <svg class="contact-icon" viewBox="0 0 16 16" aria-hidden="true"><circle cx="8" cy="8" r="6.5" fill="#d9ab3c"/><path d="M1.5 8h13M8 1.5c-3 3.5-3 9.5 0 13M8 1.5c3 3.5 3 9.5 0 13" fill="none" stroke="#141416" stroke-width="1"/></svg>
        </li>
        <li>48 Harbour Rd Lorne Vic 3232<span class="contact-icon--blank"></span></li>
      </ul>
    </div>
  </section>

</main>
</body>
</html>
```